Website for Dental Office - The Bright Arch Clinic

The bright arch clinic is a dental office offering cosmetic dentistry, general dentistry, and multi-specialty dental care all under one roof in our state-of-the-art cosmetic dental center. We are particularly striving to provide services that fit the need of the young generation. Thus, we hope to have a modern, professional concise website that represents our spirit.

*Should be able to switch from English to Chinese

6 sections besides homepage:
Home, Meet us, Services,
Patient Info, Cases&Reviews, Blog, Contact

The Services sections should contain multiple subsections such as cleaning and prevention, cosmetic dentistry, implant dentistry, removable dentures, etc...
The Patient Info section is also intended to contain several subsections such as
New Patient offer, accepted Insurance, patient portal, helpful tips, etc...

Target Market(s)

young generation

Coding

Coded - Design and coding required

Number of Pages Required

5+ page

Font styles to use
Sans Serif

Colors
0592cd
33a6d7
85cae6
00a990
33b8a4
86cfc6
cee9f5
cfeae6
3277b5

Requirements
Must have
• *Should be able to switch from English to Chinese
Nice to have
• http://www.thebrightarchclinic.com/
• As a reference, the above link is the current website, but we would like to change the appearance and the content (our new logo's picture is attached)

```html
<!DOCTYPE html>
<html lang="en">
<head>
<meta charset="utf-8">
<title>The Bright Arch Clinic</title>
<link rel="stylesheet" href="https://fonts.googleapis.com/css2?family=Lato:wght@400;700;900&display=swap">
<style>
:root{
  --blue:#0592cd;
  --blue-2:#33a6d7;
  --blue-3:#85cae6;
  --teal:#00a990;
  --teal-2:#33b8a4;
  --teal-3:#86cfc6;
  --sky:#cee9f5;
  --mint:#cfeae6;
  --navy:#3277b5;
  --heading:#1896c6;
  --text:#555f66;
  --muted:#8a949a;
  --card:#f0f1f2;
  --grey-bg:#f3f4f5;
  --white:#ffffff;
}
*{box-sizing:border-box;margin:0;padding:0}
html,body{width:1200px;height:4936px;overflow:hidden}
body{font-family:"Lato",sans-serif;color:var(--text);background:var(--white);font-size:13px;line-height:1.6}
section,header,footer{position:relative;width:1200px;overflow:hidden}
.section-title{position:absolute;left:80px;font-size:34px;font-weight:700;letter-spacing:1px;text-transform:uppercase;color:var(--heading);line-height:1}
.btn{display:inline-block;border-radius:24px;background:linear-gradient(90deg,var(--teal),var(--blue-2));color:var(--white);font-weight:700;font-size:13px;letter-spacing:1px;text-transform:uppercase;text-align:center;text-decoration:none}
.btn-view{position:absolute;left:532px;width:136px;height:42px;line-height:42px}

/* header */
.site-header{height:72px;background:var(--white);box-shadow:0 1px 4px rgba(0,0,0,.06);z-index:2}
.brand{position:absolute;left:80px;top:14px;display:flex;align-items:center;gap:12px}
.brand-mark{width:40px;height:40px;background:var(--blue);border-radius:4px}
.brand-name{font-size:15px;font-weight:700;color:var(--blue);line-height:1.15;text-transform:uppercase;width:120px}
.main-nav{position:absolute;left:360px;top:26px;display:flex;gap:30px}
.main-nav a{font-size:12px;font-weight:700;color:var(--muted);text-decoration:none;letter-spacing:.5px;text-transform:uppercase}
.main-nav a.active{color:var(--blue)}
.lang-switch{position:absolute;left:1050px;top:20px;width:66px;height:32px;border-radius:3px;background:var(--blue);color:var(--white);font-size:12px;font-weight:700;line-height:32px;text-align:center}

/* hero */
.hero{height:560px;background:linear-gradient(90deg,#f4f7f8 0%,#e9eef0 50%,#dfe6e9 100%)}
.hero-photo{position:absolute;right:0;top:0;width:640px;height:560px;background:linear-gradient(100deg,#e9eef0 0%,#d8dfe2 35%,#c9b3a6 60%,#8a6a5a 80%,#cdd6da 100%)}
.hero-copy{position:absolute;left:80px;top:222px;width:500px}
.hero-copy h1{font-size:31px;font-weight:900;color:var(--teal);letter-spacing:.5px;line-height:1.1;white-space:nowrap}
.hero-copy p{margin-top:22px;font-size:14px;color:#46525a}
.hero-copy .btn{margin-top:26px;width:220px;height:46px;line-height:46px}

/* services */
.services{height:708px}
.services .section-title{top:76px}
.service-grid{position:absolute;left:80px;top:148px;width:1040px;display:grid;grid-template-columns:repeat(3,1fr);column-gap:40px;row-gap:40px}
.service-card{height:180px;background:var(--card);padding:34px 24px 0 112px;position:relative}
.service-icon{position:absolute;left:30px;top:34px;width:58px;height:58px;border-radius:50%;background:var(--teal-2);display:flex;align-items:center;justify-content:center}
.service-card h3{font-size:14px;font-weight:700;color:var(--teal);text-transform:uppercase;letter-spacing:.5px}
.service-card p{margin-top:8px;font-size:12px;color:var(--muted);line-height:1.55}
.services .btn-view{top:614px}

/* mission */
.mission{height:860px}
.mission-band{position:absolute;left:0;top:252px;width:1200px;height:608px;background:linear-gradient(180deg,var(--teal) 0%,var(--teal-2) 30%,var(--blue) 100%)}
.mission-photo{position:absolute;left:252px;top:40px;width:696px;height:420px;background:linear-gradient(120deg,#7fc6dc 0%,#b9dbe6 40%,#d9b9a6 65%,#a77d6c 85%,#e8eef0 100%);z-index:1}
.mission-copy{position:absolute;left:200px;top:512px;width:800px;text-align:center;color:var(--white);z-index:1}
.mission-copy h2{font-size:34px;font-weight:900;letter-spacing:.5px;line-height:1.1}
.mission-copy p{margin-top:24px;font-size:12px;line-height:1.75;opacity:.95}
.mission-copy p+p{margin-top:14px}

/* team */
.team{height:700px}
.team .section-title{top:80px}
.team-grid{position:absolute;left:80px;top:132px;width:1040px;display:grid;grid-template-columns:repeat(3,1fr);gap:40px}
.team-card{height:388px;border:1px solid #e3e6e8;text-align:center;padding-top:36px}
.avatar{width:120px;height:120px;border-radius:50%;margin:0 auto;background:linear-gradient(160deg,#d9d2cc,#8b7467)}
.team-card h3{margin-top:34px;font-size:15px;font-weight:700;color:var(--teal);text-transform:uppercase;letter-spacing:.4px}
.team-card .role{font-size:12px;color:#46525a;margin-top:2px}
.team-card p.bio{margin:16px 34px 0;font-size:12px;color:var(--muted);line-height:1.6}
.team .btn-view{top:580px}

/* testimonials */
.testimonials{height:600px;background:var(--grey-bg)}
.testimonials .section-title{top:80px}
.quote-card{position:absolute;top:132px;width:500px;height:248px;background:var(--white);padding:38px 40px 0 40px}
.quote-card.left{left:80px}
.quote-card.right{left:620px}
.quote-mark{font-size:64px;line-height:.7;color:#c9ced1;font-family:"Lato",sans-serif;font-weight:900}
.quote-card p{margin-top:22px;font-size:12px;color:var(--muted);line-height:1.7}
.reviewer{position:absolute;top:428px;display:flex;align-items:center;gap:18px}
.reviewer.left{left:80px}
.reviewer.right{left:620px}
.reviewer::before{content:"";position:absolute;left:0;top:-22px;width:84px;height:3px;background:var(--teal)}
.reviewer .avatar{width:80px;height:80px;margin:0;background:linear-gradient(160deg,#d7c9bd,#7e6558)}
.reviewer h4{font-size:15px;font-weight:700;color:var(--teal);text-transform:uppercase}
.reviewer span{font-size:12px;color:var(--muted)}

/* blog */
.blog{height:640px}
.blog .section-title{top:64px}
.blog-grid{position:absolute;left:80px;top:128px;width:1040px;display:grid;grid-template-columns:repeat(3,1fr);gap:40px}
.blog-image{height:224px}
.blog-image.one{background:linear-gradient(135deg,#7cc2e0,#e7a9a4 55%,#d7dde0)}
.blog-image.two{background:linear-gradient(135deg,#c97a3a,#e8a56a 50%,#f3d9c2)}
.blog-image.three{background:linear-gradient(135deg,#e9f3f6,#a9cfdc 55%,#e4d3c8)}
.blog-date{margin-top:20px;font-size:11px;color:var(--muted)}
.blog-card h3{margin-top:8px;font-size:17px;font-weight:400;color:var(--teal);line-height:1.35}
.blog-card p{margin-top:10px;font-size:12px;color:var(--muted);line-height:1.6}

/* contact */
.contact{height:580px;background:var(--grey-bg)}
.contact .section-title{left:0;width:1200px;text-align:center;top:54px}
.contact h4{position:absolute;top:152px;font-size:14px;font-weight:700;color:#3d474e;text-transform:uppercase;letter-spacing:.5px}
.form-title{left:80px}
.info-title{left:790px}
.message-form{position:absolute;left:80px;top:192px;width:560px;display:grid;grid-template-columns:1fr 1fr;gap:14px 20px}
.field{height:44px;background:var(--white);border:1px solid #e1e4e6;padding:0 14px;font-size:11px;line-height:42px;color:#9aa2a7}
.field.area{grid-column:1/3;height:104px}
.message-form .btn{width:188px;height:44px;line-height:44px;margin-top:6px}
.contact-info{position:absolute;left:790px;top:196px;width:330px;list-style:none}
.contact-info li{display:flex;gap:22px;align-items:flex-start;margin-bottom:26px;font-size:12px;color:#46525a;line-height:1.55}
.contact-info svg{flex:0 0 28px}
.contact-info .label{font-size:11px;color:var(--muted);text-transform:uppercase}

/* footer */
.site-footer{height:216px;background:linear-gradient(180deg,var(--teal) 0%,var(--blue) 100%);text-align:center}
.social{position:absolute;left:0;top:64px;width:1200px;display:flex;justify-content:center;gap:24px}
.social span{width:48px;height:48px;border-radius:50%;border:2px solid rgba(255,255,255,.75)}
.copyright{position:absolute;left:0;top:152px;width:1200px;font-size:11px;color:rgba(255,255,255,.9);letter-spacing:.5px}
</style>
</head>
<body>

<header class="site-header">
  <div class="brand"><span class="brand-mark"></span><span class="brand-name">The Bright Arch Clinic</span></div>
  <nav class="main-nav">
    <a class="active" href="#">Home</a><a href="#">Meet us</a><a href="#">Services</a><a href="#">Patient info</a><a href="#">Cases &amp; Reviews</a><a href="#">Blog</a><a href="#">Contact</a>
  </nav>
  <div class="lang-switch">EN ▾</div>
</header>

<section class="hero">
  <div class="hero-photo" role="img" aria-label="Smiling patient seated in a dental chair"></div>
  <div class="hero-copy">
    <h1>“YOUR SMILE. OUR PASSION.”</h1>
    <p>With Northfield and Eastbrook credentials that inspire confidence, we offer cosmetic dentistry, general dentistry and multi-specialty dental care.</p>
    <a class="btn" href="#">Request appointment</a>
  </div>
</section>

<section class="services">
  <h2 class="section-title">Dental services</h2>
  <div class="service-grid">
    <div class="service-card"><span class="service-icon"><svg width="28" height="28" viewBox="0 0 28 28" fill="none" stroke="#fff" stroke-width="2"><path d="M7 5c3-2 5 0 7 0s4-2 7 0c2 2 1 7 0 9-1 3-1 9-3 9s-2-6-4-6-2 6-4 6-2-6-3-9c-1-2-2-7 0-9z"/></svg></span><h3>Cosmetic dentistry</h3><p>Lorem ipsum dolor sit amet, consectetur adipiscing elit, sed do eiusmod tempor incid.</p></div>
    <div class="service-card"><span class="service-icon"><svg width="28" height="28" viewBox="0 0 28 28" fill="none" stroke="#fff" stroke-width="2"><path d="M8 5h12l-2 7H10z"/><path d="M11 14h6M11 18h6M12 22h4"/></svg></span><h3>Implant dentistry</h3><p>Lorem ipsum dolor sit amet, consectetur adipiscing elit, sed do eiusmod tempor incid.</p></div>
    <div class="service-card"><span class="service-icon"><svg width="28" height="28" viewBox="0 0 28 28" fill="none" stroke="#fff" stroke-width="2"><rect x="4" y="10" width="6" height="8" rx="2"/><rect x="11" y="10" width="6" height="8" rx="2"/><rect x="18" y="10" width="6" height="8" rx="2"/><path d="M3 14h22"/></svg></span><h3>Orthodontics</h3><p>Lorem ipsum dolor sit amet, consectetur adipiscing elit, sed do eiusmod tempor incid.</p></div>
    <div class="service-card"><span class="service-icon"><svg width="28" height="28" viewBox="0 0 28 28" fill="none" stroke="#fff" stroke-width="2"><path d="M4 18c3-9 17-9 20 0"/><path d="M7 17c3-5 11-5 14 0"/></svg></span><h3>Clear aligners</h3><p>Lorem ipsum dolor sit amet, consectetur adipiscing elit, sed do eiusmod tempor incid.</p></div>
    <div class="service-card"><span class="service-icon"><svg width="28" height="28" viewBox="0 0 28 28" fill="none" stroke="#fff" stroke-width="2"><path d="M8 7c2-2 4 0 6 0s4-2 6 0c2 2 1 6 0 8-1 3-1 8-3 8s-2-5-3-5-1 5-3 5-2-5-3-8c-1-2-2-6 0-8z"/><path d="M11 11l2 2 4-4"/></svg></span><h3>Pediatric dentistry</h3><p>Lorem ipsum dolor sit amet, consectetur adipiscing elit, sed do eiusmod tempor incid.</p></div>
    <div class="service-card"><span class="service-icon"><svg width="28" height="28" viewBox="0 0 28 28" fill="none" stroke="#fff" stroke-width="2"><path d="M4 12c0-4 20-4 20 0v3c0 3-20 3-20 0z"/><path d="M8 12v3M12 11v4M16 11v4M20 12v3"/></svg></span><h3>Removable dentures</h3><p>Lorem ipsum dolor sit amet, consectetur adipiscing elit, sed do eiusmod tempor incid.</p></div>
  </div>
  <a class="btn btn-view" href="#">View all</a>
</section>

<section class="mission">
  <div class="mission-band"></div>
  <div class="mission-photo" role="img" aria-label="Dentist examining a patient's teeth with dental instruments"></div>
  <div class="mission-copy">
    <h2>“YOUR SMILE. OUR PASSION.”</h2>
    <p>Welcome to The Bright Arch Clinic where we specialize in General and Cosmetic Dentistry, Dental Implants, Orthodontics (Clear Aligners), Endodontics (Root Canal Treatment) and Reconstructive Dentistry for patients in the city and all of its surrounding neighborhoods, towns and nearby communities.</p>
    <p>With Northfield and Eastbrook credentials that inspire confidence, we offer cosmetic dentistry, general dentistry and multi-specialty dental care all under one roof in our state of the art cosmetic dental center conveniently located near the main station. Our specialists are dedicated to providing gentle and friendly care, and we would be honored to have you as a part of our growing family.</p>
  </div>
</section>

<section class="team">
  <h2 class="section-title">Meet our team</h2>
  <div class="team-grid">
    <div class="team-card"><div class="avatar" role="img" aria-label="Portrait of the orthodontist"></div><h3>Lena Moradi, DMD, MS</h3><div class="role">Board Certified Orthodontist</div><p class="bio">Dr. Moradi earned her dental degree from Eastbrook University School of Dental Medicine.</p></div>
    <div class="team-card"><div class="avatar" role="img" aria-label="Portrait of the orthodontist"></div><h3>Peter J. Holloway, DMD</h3><div class="role">Board Certified Orthodontist</div><p class="bio">Dr. Holloway is Board Certified by both national boards of Pediatric Dentistry and Orthodontics.</p></div>
    <div class="team-card"><div class="avatar" role="img" aria-label="Portrait of the general dentist"></div><h3>Dr. Nadia Farouk, DMD</h3><div class="role">General Dentist</div><p class="bio">Dr. Farouk earned her Doctor of Dental Medicine from Eastbrook University School of Dental Medicine.</p></div>
  </div>
  <a class="btn btn-view" href="#">View all</a>
</section>

<section class="testimonials">
  <h2 class="section-title">Testimonials</h2>
  <div class="quote-card left"><div class="quote-mark">“</div><p>Lorem ipsum dolor sit amet, consectetur adipiscing elit, sed do eiusmod tempor incididunt ut labore et dolore magna aliqua. Ut enim ad minim veniam, quis nostrud exercitation ullamco laboris nisi ut aliquip ex ea commodo consequat. Duis aute irure dolor.</p></div>
  <div class="quote-card right"><div class="quote-mark">“</div><p>Lorem ipsum dolor sit amet, consectetur adipiscing elit, sed do eiusmod tempor incididunt ut labore et dolore magna aliqua. Ut enim ad minim veniam, quis nostrud exercitation ullamco laboris nisi ut aliquip ex ea commodo consequat. Duis aute irure dolor.</p></div>
  <div class="reviewer left"><div class="avatar" role="img" aria-label="Patient portrait"></div><div><h4>Name Surname</h4><span>Lorem ipsum dolor sit amet</span></div></div>
  <div class="reviewer right"><div class="avatar" role="img" aria-label="Patient portrait"></div><div><h4>Name Surname</h4><span>Lorem ipsum dolor sit amet</span></div></div>
</section>

<section class="blog">
  <h2 class="section-title">Blog post</h2>
  <div class="blog-grid">
    <article class="blog-card"><div class="blog-image one" role="img" aria-label="Dental mirror and probe at a patient's teeth"></div><div class="blog-date">10 AUG 2019</div><h3>Lorem ipsum dolor sit amet, consectetur adipiscing elit, sed do eiusmod.</h3><p>Lorem ipsum dolor sit amet, consectetur adipiscing elit, sed do eiusmod tempor incididunt ut labore et dolore magna aliqua. Ut enim ad.</p></article>
    <article class="blog-card"><div class="blog-image two" role="img" aria-label="Young woman smiling outdoors"></div><div class="blog-date">10 AUG 2019</div><h3>Lorem ipsum dolor sit amet, consectetur adipiscing elit, sed do eiusmod.</h3><p>Lorem ipsum dolor sit amet, consectetur adipiscing elit, sed do eiusmod tempor incididunt ut labore et dolore magna aliqua. Ut enim ad.</p></article>
    <article class="blog-card"><div class="blog-image three" role="img" aria-label="Woman holding a clear aligner"></div><div class="blog-date">10 AUG 2019</div><h3>Lorem ipsum dolor sit amet, consectetur adipiscing elit, sed do eiusmod.</h3><p>Lorem ipsum dolor sit amet, consectetur adipiscing elit, sed do eiusmod tempor incididunt ut labore et dolore magna aliqua. Ut enim ad.</p></article>
  </div>
</section>

<section class="contact">
  <h2 class="section-title">Get in touch</h2>
  <h4 class="form-title">Leave a message</h4>
  <div class="message-form">
    <div class="field">Name</div><div class="field">Email</div>
    <div class="field">Phone</div><div class="field">Subject</div>
    <div class="field area">Message</div>
    <a class="btn" href="#">Submit</a>
  </div>
  <h4 class="info-title">Contact info</h4>
  <ul class="contact-info">
    <li><svg width="28" height="28" viewBox="0 0 28 28"><path d="M14 2a9 9 0 0 0-9 9c0 7 9 15 9 15s9-8 9-15a9 9 0 0 0-9-9z" fill="#00a990"/><circle cx="14" cy="11" r="3.5" fill="#fff"/></svg><div>4120 Harbor Lane, Suite 210<br>Millbrook MA 02100</div></li>
    <li><svg width="28" height="28" viewBox="0 0 28 28"><path d="M7 3l5 5-3 3c1 3 5 7 8 8l3-3 5 5-3 4C12 24 4 16 3 6z" fill="#00a990"/></svg><div><span class="label">Call us</span><br>555.201.4480</div></li>
    <li><svg width="28" height="28" viewBox="0 0 28 28"><rect x="3" y="6" width="22" height="16" rx="2" fill="#00a990"/><path d="M4 8l10 7 10-7" fill="none" stroke="#fff" stroke-width="2"/></svg><div><span class="label">Email us</span><br>info@brightarchclinic.com</div></li>
  </ul>
</section>

<footer class="site-footer">
  <div class="social"><span></span><span></span><span></span><span></span></div>
  <div class="copyright">© THE BRIGHT ARCH CLINIC 2019. All Rights Reserved</div>
</footer>

</body>
</html>
```